VitaBraid Web Design. Health and Wellness Industry

We are in process of creating next big Cloud based Health Care Management system. We have created 1st draft of Landing Page design. It is missing curb appeal, jazzy feel and engaging modern look.

Need a talented designer to recreate UI/ UX and take it to the next level.
If you are a creative designer, gifted with vision and imagination, I strongly encourage you to participate.

I want the designers to stay focus on the Landing page
Once we select the winner we will provide other subsequent pages
Follow up pages will be similar simple design

Target Market(s)

Individual Users and small business
Age Group 35-75
Individuals involved in "Health and Fitness" activity tracking, managing etc.

Industry/Entity Type

Health And Wellness

Number of Pages Required

5+ page

Colors
f68e4e
34a6d7

Requirements
Must have
• Super Engaging UI/ UX
• Smart and Contemporary look
• Easy to Navigate
• Folder Style menu bar
• Slideshow
• Social Medial Friendly
• Online Shopping
Nice to have
• Start from the enclosed draft Landing Page Idea.
• Feel Free to include additional frame, information section, Icon etc.

```html
<!DOCTYPE html>
<html lang="en">
<head>
<meta charset="utf-8">
<title>VitaBraid – Health Management Starts Here</title>
<link href="https://fonts.googleapis.com/css2?family=Open+Sans:wght@400;600;700&display=swap" rel="stylesheet">
<style>
:root{
  --orange:#f37b26;
  --orange-light:#f68e4e;
  --orange-deep:#d9641a;
  --brown-dark:#2e170d;
  --brown:#4a2414;
  --green:#7cb82f;
  --ink:#333;
  --muted:#777;
  --grey-bg:#f3f3f3;
  --white:#fff;
}
*{box-sizing:border-box;margin:0;padding:0}
html,body{width:1200px;height:2780px;overflow:hidden}
body{font-family:"Open Sans",Arial,sans-serif;color:var(--ink);background:var(--white);font-size:14px}
.container{width:1000px;margin:0 auto;position:relative}

/* header */
.site-header{height:120px;background:var(--orange)}
.site-header .container{height:120px}
.brand{position:absolute;left:0;top:20px;display:flex;align-items:center;gap:12px;color:var(--white);font-weight:700;font-size:38px}
.brand-dot{width:44px;height:44px;border-radius:50%;background:var(--white)}
.brand-tag{position:absolute;left:56px;top:70px;color:var(--white);font-size:12px;letter-spacing:1px}
.top-bar{position:absolute;right:0;top:14px;display:flex;align-items:center;gap:14px;color:var(--white);font-size:13px}
.btn-emergency{border:2px solid var(--white);background:var(--orange-deep);color:var(--white);padding:5px 14px;font-weight:600;font-size:13px}
.flag{width:18px;height:12px;background:var(--white);display:inline-block}
.main-nav{position:absolute;right:0;top:66px;display:flex;align-items:center;gap:28px}
.main-nav a{color:var(--white);text-decoration:none;font-weight:600;font-size:15px}
.main-nav .search{width:30px;height:30px;border-radius:50%;background:var(--white);display:flex;align-items:center;justify-content:center}

/* hero */
.hero{height:520px;position:relative;overflow:hidden;background:linear-gradient(90deg,#efe6df 0%,#d9b59a 30%,#b2673a 55%,#c55a1d 100%)}
.hero-photo{position:absolute;left:0;top:0;width:420px;height:520px;background:linear-gradient(90deg,#f4eee9,#d7b9a3)}
.hero-art{position:absolute;right:150px;top:130px;width:240px;height:200px;border-radius:40px;background:linear-gradient(180deg,#9fd4ee,#4aa5d6)}
.hero-copy{position:absolute;left:440px;top:110px;width:380px;color:var(--white)}
.hero-copy .brand-name{font-size:56px;font-weight:700;display:flex;align-items:center;gap:12px}
.hero-copy .brand-name i{width:40px;height:40px;border-radius:50%;background:var(--white);display:block}
.hero-copy h2{font-size:22px;font-weight:600;margin:14px 0 10px}
.hero-copy p{font-size:14px;line-height:1.55}
.btn-outline{display:inline-block;margin-top:24px;border:2px solid var(--white);color:var(--white);padding:10px 24px;font-size:18px;font-weight:600}
.slide-arrow{position:absolute;top:240px;width:40px;height:40px;border-radius:50%;background:var(--white);display:flex;align-items:center;justify-content:center}
.slide-arrow.prev{left:30px}.slide-arrow.next{right:30px}

/* about */
.about{height:420px;padding-top:100px}
.about-art{position:absolute;left:20px;top:0;width:240px;height:240px;border-radius:50%;background:radial-gradient(circle,#fbd9c2 0%,#f7b98f 70%,#f3a56f 100%)}
.about-text{margin-left:300px}
.about-text h2{font-size:30px;font-weight:600;color:var(--ink);margin-bottom:14px}
.about-text .lead{font-size:16px;line-height:1.6;color:#555;margin-bottom:16px}
.about-text p{font-size:13px;line-height:1.7;color:var(--muted)}

/* services */
.services{height:440px;background:linear-gradient(180deg,var(--brown-dark),#5b2a12 60%,var(--brown-dark));color:var(--white);text-align:center;padding-top:46px}
.section-title{font-size:30px;font-weight:600}
.services .section-title{margin-bottom:40px}
.service-grid{display:flex;justify-content:space-between}
.service{width:220px}
.service-icon{width:78px;height:78px;border-radius:50%;border:2px solid var(--orange-light);margin:0 auto 18px;display:flex;align-items:center;justify-content:center}
.service.active .service-icon{background:var(--orange)}
.service h3{font-size:18px;font-weight:600;margin-bottom:10px}
.service p{font-size:12px;line-height:1.6;color:#e6d2c6}
.btn-small{display:inline-block;margin-top:14px;background:var(--orange);color:var(--white);font-size:12px;font-weight:600;padding:5px 16px;border-radius:3px}

/* products */
.products{height:420px;background:var(--grey-bg);text-align:center;padding-top:44px}
.products .section-title{color:var(--ink);margin-bottom:30px}
.product-grid{display:flex;justify-content:center;gap:60px}
.product-card{width:240px;background:var(--white);box-shadow:0 2px 8px rgba(0,0,0,.15);text-align:left}
.product-photo{height:140px;margin:14px;border-radius:4px}
.product-name{background:#ddd;color:#555;font-size:12px;text-align:center;padding:6px;margin:0 14px}
.product-desc{font-size:12px;color:var(--muted);padding:10px 14px 6px;line-height:1.5}
.product-foot{display:flex;justify-content:space-between;align-items:center;padding:4px 14px 16px}
.price{color:var(--orange);font-weight:700;font-size:18px}
.btn-buy{background:var(--green);color:var(--white);font-size:13px;font-weight:600;padding:5px 14px;border-radius:3px}

/* stories */
.stories{height:480px;background:linear-gradient(180deg,#6b3418,var(--brown) 50%,#3a1b0e);padding-top:54px}
.stories .section-title{color:var(--white);margin-bottom:44px;text-align:center}
.story-grid{display:flex;justify-content:space-between}
.story{position:relative;width:300px;height:170px;background:var(--orange);border-radius:4px;padding:22px 18px 0 108px;color:var(--white)}
.story-photo{position:absolute;left:-16px;top:24px;width:110px;height:110px;border-radius:50%;border:4px solid var(--white);background:linear-gradient(180deg,#c9a48d,#6e4b3a)}
.story p{font-size:12px;line-height:1.55}
.story .who{font-weight:700;font-size:13px;margin-top:6px}
.story .btn-small{background:var(--brown);margin-top:10px}

/* footer */
.site-footer{height:340px;background:var(--orange);color:var(--white);padding-top:46px}
.footer-grid{display:flex;justify-content:space-between}
.footer-col{width:220px}
.footer-col h4{font-size:16px;font-weight:700;margin-bottom:16px;text-transform:uppercase}
.footer-col li{list-style:none;font-size:13px;line-height:2;display:flex;align-items:center;gap:8px}
.footer-col .tweet{font-size:12px;line-height:1.55;margin-bottom:14px}
.footer-col .tweet span{display:block;opacity:.85;font-size:11px}
.sq{width:12px;height:12px;background:var(--white);display:inline-block}
.phone{font-size:20px;font-weight:700}
.copyright{height:40px;background:var(--orange-deep);color:var(--white);font-size:12px;text-align:center;line-height:40px}
</style>
</head>
<body>

<header class="site-header">
  <div class="container">
    <div class="brand"><span class="brand-dot"></span>VitaBraid</div>
    <div class="brand-tag">Health management starts here</div>
    <div class="top-bar">
      <span class="btn-emergency">Emergency Login</span>
      <span>Login</span><span>|</span><span>Create an Account</span><span>|</span>
      <span>Country <i class="flag"></i></span>
    </div>
    <nav class="main-nav">
      <a href="#">Home</a>
      <a href="#">Discover Health Vault</a>
      <a href="#">Shop</a>
      <a href="#">Caregiver</a>
      <a href="#">Community</a>
      <span class="search"><svg width="14" height="14" viewBox="0 0 14 14"><circle cx="6" cy="6" r="4.2" fill="none" stroke="#f37b26" stroke-width="2"/><line x1="9" y1="9" x2="13" y2="13" stroke="#f37b26" stroke-width="2"/></svg></span>
    </nav>
  </div>
</header>

<section class="hero">
  <div class="hero-photo" role="img" aria-label="Doctor in a white coat holding a stethoscope"></div>
  <div class="hero-art" role="img" aria-label="Cloud with a stethoscope illustration"></div>
  <div class="hero-copy">
    <div class="brand-name"><i></i>VitaBraid</div>
    <h2>Health Management Starts Here</h2>
    <p>Track your daily health data in one secure place, share records with your care team, and stay on top of every visit and goal.</p>
    <span class="btn-outline">Learn More</span>
  </div>
  <span class="slide-arrow prev"><svg width="12" height="14" viewBox="0 0 12 14"><path d="M9 1 3 7l6 6" fill="none" stroke="#555" stroke-width="2.5"/></svg></span>
  <span class="slide-arrow next"><svg width="12" height="14" viewBox="0 0 12 14"><path d="M3 1l6 6-6 6" fill="none" stroke="#555" stroke-width="2.5"/></svg></span>
</section>

<section class="about">
  <div class="container">
    <div class="about-art" role="img" aria-label="Cloud with medical tools and devices illustration"></div>
    <div class="about-text">
      <h2>About Our VitaBraid</h2>
      <p class="lead">Bring every record, reading and reminder together in a single cloud vault built for families and small practices.</p>
      <p>Upload lab results, log activity, follow medication plans and invite caregivers to help. Your data stays private, backed up and ready on any device whenever you need it most, at home, at work or on the road.</p>
    </div>
  </div>
</section>

<section class="services">
  <div class="container">
    <h2 class="section-title">Our Services</h2>
    <div class="service-grid">
      <div class="service active">
        <div class="service-icon"><svg width="34" height="34" viewBox="0 0 34 34"><path d="M4 16 30 4 18 30l-3-11z" fill="#fff"/></svg></div>
        <h3>Overview</h3>
        <p>Short notes on how this part of the service helps you plan care.</p>
        <span class="btn-small">Read More</span>
      </div>
      <div class="service">
        <div class="service-icon"><svg width="34" height="34" viewBox="0 0 34 34"><circle cx="17" cy="17" r="9" fill="none" stroke="#f68e4e" stroke-width="3"/><circle cx="17" cy="17" r="3" fill="#f68e4e"/></svg></div>
        <h3>How it Works</h3>
        <p>Short notes on how this part of the service helps you plan care.</p>
        <span class="btn-small">Read More</span>
      </div>
      <div class="service">
        <div class="service-icon"><svg width="34" height="34" viewBox="0 0 34 34"><path d="M17 4l4 9 9 1-7 6 2 10-8-5-8 5 2-10-7-6 9-1z" fill="none" stroke="#f68e4e" stroke-width="2.5"/></svg></div>
        <h3>Stories</h3>
        <p>Short notes on how this part of the service helps you plan care.</p>
        <span class="btn-small">Read More</span>
      </div>
      <div class="service">
        <div class="service-icon"><svg width="34" height="34" viewBox="0 0 34 34"><path d="M6 18l7 7 15-16" fill="none" stroke="#f68e4e" stroke-width="3.5"/></svg></div>
        <h3>Get Started</h3>
        <p>Short notes on how this part of the service helps you plan care.</p>
        <span class="btn-small">Read More</span>
      </div>
    </div>
  </div>
</section>

<section class="products">
  <h2 class="section-title">Feature Products</h2>
  <div class="product-grid">
    <div class="product-card">
      <div class="product-photo" role="img" aria-label="White handheld health monitor" style="background:linear-gradient(180deg,#fafafa,#dcdcdc)"></div>
      <div class="product-name">Handheld Pulse Monitor</div>
      <p class="product-desc">Smart reading, app sync and long battery life.</p>
      <div class="product-foot"><span class="price">$29.95</span><span class="btn-buy">Buy Now »</span></div>
    </div>
    <div class="product-card">
      <div class="product-photo" role="img" aria-label="Blue and white water purifier" style="background:linear-gradient(180deg,#eef6fb,#9cc8e4)"></div>
      <div class="product-name">Home Water Filter</div>
      <p class="product-desc">Smart reading, app sync and long battery life.</p>
      <div class="product-foot"><span class="price">$29.95</span><span class="btn-buy">Buy Now »</span></div>
    </div>
    <div class="product-card">
      <div class="product-photo" role="img" aria-label="Black glass body weight scale" style="background:linear-gradient(180deg,#f2f2f2,#2b2b2b)"></div>
      <div class="product-name">Digital Body Scale</div>
      <p class="product-desc">Smart reading, app sync and long battery life.</p>
      <div class="product-foot"><span class="price">$29.95</span><span class="btn-buy">Buy Now »</span></div>
    </div>
  </div>
</section>

<section class="stories">
  <div class="container">
    <h2 class="section-title">Find out ways people are using VitaBraid Health Vault</h2>
    <div class="story-grid">
      <div class="story">
        <div class="story-photo" role="img" aria-label="Portrait of a customer"></div>
        <p>I keep all my test results here and my doctor sees them before every visit.</p>
        <p class="who">Dana Whitlow</p>
        <span class="btn-small">Read More</span>
      </div>
      <div class="story">
        <div class="story-photo" role="img" aria-label="Portrait of a customer"></div>
        <p>I keep all my test results here and my doctor sees them before every visit.</p>
        <p class="who">Marcus Reyne</p>
        <span class="btn-small">Read More</span>
      </div>
      <div class="story">
        <div class="story-photo" role="img" aria-label="Portrait of a customer"></div>
        <p>I keep all my test results here and my doctor sees them before every visit.</p>
        <p class="who">Lena Ostrov</p>
        <span class="btn-small">Read More</span>
      </div>
    </div>
  </div>
</section>

<footer class="site-footer">
  <div class="container footer-grid">
    <div class="footer-col">
      <h4>Links</h4>
      <ul>
        <li>› Sitemap</li>
        <li>› Terms &amp; Conditions</li>
        <li>› Privacy Policy</li>
        <li>› Help</li>
      </ul>
    </div>
    <div class="footer-col">
      <h4>Latest Tweets</h4>
      <p class="tweet">Just shipped new sleep charts to the vault, take a look today<span>2 hours ago</span></p>
      <p class="tweet">Just shipped new sleep charts to the vault, take a look today<span>5 hours ago</span></p>
    </div>
    <div class="footer-col">
      <h4>Contact Us</h4>
      <ul>
        <li>18 Willow Court, Brookfield</li>
        <li class="phone">555-014-2290</li>
        <li>hello@vitabraid.example</li>
      </ul>
    </div>
    <div class="footer-col">
      <h4>Social Media</h4>
      <ul>
        <li><i class="sq"></i>Friendbook</li>
        <li><i class="sq"></i>Chirper</li>
        <li><i class="sq"></i>Circles Plus</li>
        <li><i class="sq"></i>Tubecast</li>
      </ul>
    </div>
  </div>
</footer>
<div class="copyright">Copyright © 2024 VitaBraid. All rights reserved.</div>

</body>
</html>
```